Hardcore nerd needs to stand out in a sea of dull Defence business cards

Wombarra Devices is a new Australian consulting engineering company that turns research and theory into practical systems. No evangelistic fluff, just mathematics and physics into electronic and optical circuits for consumer products, scientific research or Defence applications.

We already have a recognised logo (provided) which is often dark blue/black on a light background but we're open to other combinations. (Us engineers tend to have limited aesthetic imagination :)

Some of our recent products have included:
* Instrumentation for electrical testing,
* Radar jammers,
* GPS antenna design,
* Satellite tracking systems,
* High power lasers

We're open to both single and double-sided designs - happy to be convinced either way.

P.S. Another group is working on the web page, so - alas - our web site is currently of no use for images/ideas...

Target Market(s)

Engineering managers,
Scientists

Contact Information for Business Card

Dr Colin Harte
R&D Engineer

colin@wombarradevices.com.au
0427 563 710

PO Box XXX (to be confirmed)
Kelsby ACT 2917
Australia

Font styles to use
Serif
Sans Serif

Colors

Designer to choose colors to be used in the design.

Requirements
Must have
• My contact details!
• I've had many (great) "bold and plain" designs submitted already, so feel free to be artistically creative :)
• Happy to take advice re fonts/colours/printability etc.
Nice to have
• I'm not sure if "lists" are more at home on a CV than a business card, but representative services include:
• Applied electromagnetics
• RF and high speed electronics
• Signal and image processing
• Electro-optical and laser systems
• Concept-to-prototype design services
• If you're considering double sided cards, then often measuring/alignment grids/rulers feature on the back of similar cards.
• e.g. https://www.veltranoptics.example/newgrouppage9.cfm?objectgroup_id=4183
• https://www.veltranoptics.example/newgrouppage9.cfm?objectgroup_ID=4185
• ..or even a "Smith chart" (google will return lots)
• Generic images to represent a capability might work - googling images associated with keyword for each of these areas might help:
• - "passive radar", "phased array", "fdtd", "vircator"
• RF and high speed electronic design
• - "smith chart", "microstrip circuits", "dimensioned drawing", "electronic schematic"
• - "dft", "iir filter"
• - "optical cavity". "laser energy level diagram"
• Background/watermarked images outlines/wireframes/schematics would probably look OK.
Should not have
• If a list of projects/services is provided, it is important not to make the client feel that this is "all" the company can do. Engineering design is a creative discipline (like graphics :)
• Please, no stock "military" snaps like planes, missiles, etc!

```html
<!DOCTYPE html>
<html lang="en">
<head>
<meta charset="utf-8">
<title>Wombarra Devices – Business Card</title>
<link href="https://fonts.googleapis.com/css2?family=Lato:wght@400;700;900&family=Arimo:wght@700&display=swap" rel="stylesheet">
<style>
  :root {
    --backdrop: #2b2b2b;
    --card: #141414;
    --ink: #ffffff;
    --ink-soft: #d9d9d9;
    --rule: #6a6a6a;
    --pattern-top: #2c2c2c;
    --pattern-mid: #232323;
    --pattern-bottom: #141414;
  }
  * { box-sizing: border-box; margin: 0; padding: 0; }
  html, body { width: 1200px; height: 1108px; overflow: hidden; }
  body {
    background: var(--backdrop);
    font-family: "Lato", sans-serif;
    color: var(--ink);
    display: flex;
    justify-content: center;
    align-items: center;
    gap: 80px;
  }
  .card {
    width: 440px;
    height: 720px;
    background: var(--card);
    border-radius: 26px;
    position: relative;
    overflow: hidden;
    box-shadow: 0 10px 30px rgba(0,0,0,.45);
  }

  /* Front */
  .brand {
    position: absolute;
    top: 118px;
    left: 44px;
    display: flex;
    align-items: center;
    gap: 16px;
  }
  .brand-dot {
    width: 58px; height: 58px;
    border-radius: 50%;
    background: var(--ink);
    flex: none;
  }
  .brand-name {
    font-weight: 900;
    font-size: 36px;
    line-height: 1.05;
    text-transform: uppercase;
    letter-spacing: 1px;
    color: var(--ink);
  }
  .person {
    position: absolute;
    top: 400px;
    left: 0; right: 0;
    text-align: center;
  }
  .person-name {
    font-family: "Arimo", sans-serif;
    font-weight: 700;
    font-size: 25px;
    letter-spacing: .5px;
    text-transform: uppercase;
  }
  .person-role {
    font-size: 17px;
    color: var(--ink-soft);
    margin-top: 2px;
  }
  .icon-rule {
    display: flex;
    align-items: center;
    justify-content: center;
    gap: 6px;
    margin: 8px auto 6px;
    width: 280px;
  }
  .icon-rule .line { flex: 1; height: 1px; background: var(--rule); }
  .icon {
    width: 22px; height: 22px;
    border-radius: 50%;
    background: var(--ink);
    display: flex; align-items: center; justify-content: center;
  }
  .contact { font-size: 18px; line-height: 1.3; }
  .divider { width: 280px; height: 1px; background: var(--rule); margin: 12px auto; }
  .address { font-size: 18px; line-height: 1.3; }

  /* Back */
  .pattern {
    position: absolute;
    top: 0; left: 0; right: 0;
    height: 520px;
    background: linear-gradient(180deg, var(--pattern-top) 0%, var(--pattern-mid) 55%, var(--pattern-bottom) 100%);
  }
  .back-mark {
    position: absolute;
    top: 480px; left: 0; right: 0;
    display: flex; align-items: center; justify-content: center;
    gap: 10px;
  }
  .back-mark .brand-dot { width: 30px; height: 30px; }
  .back-mark .brand-name { font-size: 17px; }
  .services {
    position: absolute;
    top: 548px; left: 0; right: 0;
    list-style: none;
    text-align: center;
    font-size: 19px;
    line-height: 1.3;
  }
</style>
</head>
<body>

<section class="card card-front">
  <div class="brand">
    <span class="brand-dot"></span>
    <span class="brand-name">Wombarra<br>Devices</span>
  </div>

  <div class="person">
    <h1 class="person-name">Dr Colin Harte</h1>
    <p class="person-role">R&amp;D Engineer</p>

    <div class="icon-rule">
      <span class="line"></span>
      <span class="icon" aria-label="phone">
        <svg width="12" height="12" viewBox="0 0 24 24"><path d="M6.6 10.8a15 15 0 0 0 6.6 6.6l2.2-2.2c.3-.3.7-.4 1-.2 1.1.4 2.3.6 3.6.6.6 0 1 .4 1 1V20c0 .6-.4 1-1 1A17 17 0 0 1 3 4c0-.6.4-1 1-1h3.5c.6 0 1 .4 1 1 0 1.3.2 2.5.6 3.6.1.3 0 .7-.2 1z" fill="#141414"/></svg>
      </span>
      <span class="icon" aria-label="email">
        <svg width="12" height="12" viewBox="0 0 24 24"><rect x="2" y="5" width="20" height="14" fill="none" stroke="#141414" stroke-width="2.5"/><path d="M2 5l10 8 10-8" fill="none" stroke="#141414" stroke-width="2.5"/></svg>
      </span>
      <span class="icon" aria-label="website">
        <svg width="12" height="12" viewBox="0 0 24 24"><circle cx="12" cy="12" r="9" fill="none" stroke="#141414" stroke-width="2.5"/><path d="M3 12h18M12 3c3 3 3 15 0 18M12 3c-3 3-3 15 0 18" fill="none" stroke="#141414" stroke-width="2"/></svg>
      </span>
      <span class="line"></span>
    </div>

    <p class="contact">0427 563 710</p>
    <p class="contact">colin@wombarradevices.com.au</p>
    <p class="contact">www.wombarradevices.com.au</p>

    <div class="divider"></div>

    <p class="address">PO Box XXX</p>
    <p class="address">Kelsby ACT 2917, Australia</p>
  </div>
</section>

<section class="card card-back">
  <div class="pattern" role="img" aria-label="Faint tiled brand mark watermark pattern fading towards the bottom"></div>
  <div class="back-mark">
    <span class="brand-dot"></span>
    <span class="brand-name">Wombarra Devices</span>
  </div>
  <ul class="services">
    <li>Applied electromagnetics</li>
    <li>RF and high speed electronics</li>
    <li>Signal and image processing</li>
    <li>Electro-optical and laser systems</li>
  </ul>
</section>

</body>
</html>
```